Web Design Project - Shipping Industry

Goals and Objectives
The objective of the new website is to create a more modern look and feel. The site will also allow for a more effective means of communicating with members while providing the public with information and developments in the local, regional and international shipping industry.
Scope
The website will highlight the history of the organisation inclusive of text and photographs. It will take visitors through the years from beginning to present. Information on the history of the shipping industry will also be included.
It will feature current articles on the organisation, its members and stakeholders in the shipping industry. Member information as well as pertinent details regarding the organisation’s subsidiaries will be documented for the website.
Information as it relates to shipping statistics, case studies, laws and regulations, international treaties and trade documents, shipping terms, careers in shipping, job opportunities, training opportunities, information for shippers including port listing and trade lanes will be main features of the content for the website.
The Association’s community involvement, industry calendar events and related links relevant industry members will also be featured.
Target Market
• The General Public;
• Members of the organization;
• Shipping Industry Stakeholders (local, regional and international);
• Tertiary students conducting research.
• Potential employees
• Potential Business Partners
Best Practice Bench Marketing
The following websites are being looked at:
• Korvel Quayworks - http://www.korvelquayworks.example/ (preferred look)
• Tessaly Maritime Association - http://www.tma-freight.example/ (like image transition on main page)
• Drovna - http://www.drovna.example (professional look)
• PLW - http://www.pelworth.example (preferred color: blue in logo)
• Quillo - http://www.quillo.example/electronics/tv-video-audio/ (preferred look for links page: image + short text below + visit site link)
Expected Result
• 3 - 5 pages which must include: [1] main page [2] standard page [3] links page

```html
<!DOCTYPE html>
<html lang="en">
<head>
<meta charset="utf-8">
<title>Harbourline Data Services</title>
<link rel="stylesheet" href="https://fonts.googleapis.com/css2?family=Source+Sans+3:ital,wght@0,400;0,600;0,700;1,400&display=swap">
<style>
:root{
  --page:#ececec;
  --white:#ffffff;
  --navy:#0e2a7a;
  --nav-top:#1d49b8;
  --blue:#1f5fc8;
  --band:#2a67d4;
  --gold:#f2c20f;
  --ink:#1b1b1b;
  --muted:#7a7a7a;
  --rule:#d8d8d8;
  --placeholder:#dcdfe4;
}
*{box-sizing:border-box;margin:0;padding:0}
html,body{width:1148px;height:1200px;overflow:hidden}
body{background:var(--page);font-family:"Source Sans 3",Arial,sans-serif;color:var(--ink)}
.sheet{position:absolute;left:100px;top:0;width:949px;height:1200px;background:var(--white);box-shadow:0 0 6px rgba(0,0,0,.12)}
.abs{position:absolute}
.account-links{left:914px;top:11px;font-size:14px;width:96px;text-align:right}
.account-links span{margin:0 6px}
.brand{left:135px;top:52px;font-size:32px;font-weight:600;letter-spacing:6px;color:var(--navy)}
.social{left:724px;top:63px;display:flex;gap:5px}
.social i{display:block;width:14px;height:14px;background:var(--blue);border-radius:2px}
.search{left:804px;top:57px;width:213px;height:25px;border:1px solid #cfcfcf;font-size:12.5px;padding:5px 10px}
.search svg{position:absolute;right:8px;top:5px}
.main-nav{left:133px;top:121px;width:883px;height:41px;border-top:3px solid var(--gold);background:linear-gradient(var(--nav-top),var(--navy));display:flex;justify-content:space-around;align-items:center}
.main-nav a{color:var(--white);font-weight:700;font-size:12px;text-decoration:none;letter-spacing:.2px}
.hero{left:133px;top:162px;width:883px;height:300px;display:flex}
.hero div{flex:1}
.hero-left{background:linear-gradient(135deg,#c8d3de,#4d6f9a 55%,#c96a3a)}
.hero-right{background:linear-gradient(160deg,#b9c3cc,#d96e36 60%,#8a6c55)}
.hero-band{left:133px;top:462px;width:883px;height:70px;background:linear-gradient(var(--band),#1f55c0);color:var(--white)}
.hero-band h1{position:absolute;left:22px;top:15px;font-weight:400;font-size:33px}
.hero-band p{position:absolute;left:405px;top:13px;font-size:14.5px;line-height:20px;width:460px}
.more-light{font-weight:600;font-size:13px;margin-left:6px}
.arrow{display:inline-block;vertical-align:-3px;margin-left:5px}
.intro-mark{left:151px;top:566px;width:62px;height:62px;background:var(--placeholder)}
.intro{left:246px;top:570px;width:590px;font-size:16px;line-height:21px;color:#444;letter-spacing:-.1px}
.intro b{font-weight:400;color:var(--ink)}
.login{left:865px;top:552px;width:135px}
.login h3{color:var(--blue);font-size:12.5px;font-weight:700;margin-bottom:6px}
.login .field{height:25px;border:1px solid #cfcfcf;font-size:12.5px;padding:4px 7px;margin-bottom:9px}
.login small{font-size:10px;display:block}
.news{left:145px;top:674px;width:275px}
.news h2{color:var(--blue);font-size:20px;font-weight:700;margin-bottom:8px}
.news article{margin-bottom:15px}
.news h4{font-size:13.5px;font-weight:600;line-height:18px}
.news time{display:block;font-style:italic;color:var(--muted);font-size:13px;margin:2px 0 5px}
.news p{font-size:12.5px;line-height:17.7px}
.news a,.card a{color:var(--blue);font-weight:600;text-decoration:none}
.card{left:460px;width:359px;height:130px}
.card .photo{position:absolute;left:0;top:0;width:167px;height:107px}
.card h3{position:absolute;left:181px;top:-2px;color:var(--blue);font-size:13.5px;font-weight:700}
.card p{position:absolute;left:181px;top:22px;width:178px;font-size:10px;line-height:14px}
.card a{position:absolute;left:181px;top:92px;font-size:11.5px}
.card-rule{left:460px;width:359px;height:1px;background:var(--rule)}
.partners{left:867px;top:680px;width:150px;display:flex;flex-direction:column;gap:32px}
.partners span{font-size:13px;font-weight:700;color:var(--navy);display:flex;align-items:center;gap:6px;height:34px;white-space:nowrap}
.partners span i{display:block;width:12px;height:12px;background:var(--blue);flex:none}
.footer{left:133px;top:1120px;width:883px;height:44px;background:linear-gradient(var(--nav-top),var(--navy));color:var(--white);font-size:10.5px}
.footer .copy{position:absolute;left:13px;top:16px}
.footer nav{position:absolute;right:22px;top:16px}
.footer nav span{margin:0 11px}
</style>
</head>
<body>
<div class="sheet"></div>

<div class="abs account-links">Register<span>|</span>Login</div>
<div class="abs brand">NAVITERM</div>
<div class="abs social" aria-label="Social links"><i></i><i></i><i></i><i></i></div>
<div class="abs search">Search
  <svg width="14" height="14" viewBox="0 0 14 14"><circle cx="8" cy="6" r="4.5" fill="none" stroke="#bbb" stroke-width="1.5"/><line x1="4.8" y1="9.2" x2="1" y2="13" stroke="#bbb" stroke-width="2"/></svg>
</div>

<nav class="abs main-nav">
  <a>HOME</a><a>ABOUT US</a><a>PRODUCTS</a><a>SERVICES</a><a>NEWS</a><a>SUPPORT</a><a>PARTNERS</a><a>CUSTOMERS</a><a>CONTACT</a>
</nav>

<div class="abs hero">
  <div class="hero-left" role="img" aria-label="Two engineers in hard hats reviewing a laptop beside stacked shipping containers"></div>
  <div class="hero-right" role="img" aria-label="Port workers in safety vests walking beneath a container crane"></div>
</div>
<div class="abs hero-band">
  <h1>Harbourline Data Services</h1>
  <p>Built for operation in a port or agent environment, it is a powerful platform to manage their operations and drive efficiencies <span class="more-light">LEARN MORE</span><svg class="arrow" width="15" height="15" viewBox="0 0 16 16"><circle cx="8" cy="8" r="7" fill="#fff"/><path d="M4 8h7M8 5l3 3-3 3" stroke="#1f55c0" stroke-width="2" fill="none"/></svg></p>
</div>

<div class="abs intro-mark" role="img" aria-label="Company emblem"></div>
<p class="abs intro"><b>Harbourline Data Services</b> (NAVITERM), a subsidiary of the Meridian Shipping Association, was established in 1981 to provide information technology infrastructure and systems support to the local port community and the wider Caribbean maritime sector.</p>

<aside class="abs login">
  <h3>MEMEBR LOGIN</h3>
  <div class="field">Username</div>
  <div class="field">Password</div>
  <small>&nbsp;Register &nbsp;&nbsp;| &nbsp;&nbsp;Forgot Password?</small>
</aside>

<section class="abs news">
  <h2>LATEST NEWS</h2>
  <article>
    <h4>HDS Launches Document Management Software</h4>
    <time>March 10, 2012</time>
    <p>Harbourline Data Services Limited (HDS), along with its partner Larkfield Systems Incorporated, presented the Stratum Enterprise Document Management Software durind... <a>Read more »</a></p>
  </article>
  <article>
    <h4>Business Continuity - Are you prepared ?</h4>
    <time>March 8, 2012</time>
    <p>Business continuity should be the number one priority of every organization, since failure to have a contingency plan has repeatedly... <a>Read more »</a></p>
  </article>
  <article>
    <h4>Marisa Delane Returned As Customs Brokers President</h4>
    <time>March 8, 2012</time>
    <p>Business continuity should be the number one priority of every organization, since failure to have a contingency plan has repeatedly... <a>Read more »</a></p>
  </article>
</section>

<div class="abs card" style="top:679px">
  <div class="photo" role="img" aria-label="Trainer and trainee reviewing plans in a warehouse" style="background:linear-gradient(135deg,#b89a78,#6f7f8c)"></div>
  <h3>TRAINING OPPORTUNITIES</h3>
  <p>Lorem ipsum dolor sit amet, consectetur adipisicing elit, sed do eiusmod tempor incididunt ut labore et dolore magna aliqua. Ut enim ad minim veniam, quis</p>
  <a>LEARN MORE <svg class="arrow" width="14" height="14" viewBox="0 0 16 16"><circle cx="8" cy="8" r="7" fill="#1f5fc8"/><path d="M4 8h7M8 5l3 3-3 3" stroke="#fff" stroke-width="2" fill="none"/></svg></a>
</div>
<div class="abs card-rule" style="top:804px"></div>
<div class="abs card" style="top:827px">
  <div class="photo" role="img" aria-label="Operator working at a control room console with monitors" style="background:linear-gradient(135deg,#8a7a5e,#3f5a5a)"></div>
  <h3>JOB OPPORTUNITIES</h3>
  <p>Lorem ipsum dolor sit amet, consectetur adipisicing elit, sed do eiusmod tempor incididunt ut labore et dolore magna aliqua. Ut enim ad minim veniam, quis</p>
  <a>LEARN MORE <svg class="arrow" width="14" height="14" viewBox="0 0 16 16"><circle cx="8" cy="8" r="7" fill="#1f5fc8"/><path d="M4 8h7M8 5l3 3-3 3" stroke="#fff" stroke-width="2" fill="none"/></svg></a>
</div>
<div class="abs card-rule" style="top:956px"></div>
<div class="abs card" style="top:975px">
  <div class="photo" role="img" aria-label="Dock workers in orange vests walking along a quay beside a ship" style="background:linear-gradient(160deg,#a9b7c4,#d0793e 60%,#7b6a58)"></div>
  <h3>CAREERS IN SHIPPING</h3>
  <p>Lorem ipsum dolor sit amet, consectetur adipisicing elit, sed do eiusmod tempor incididunt ut labore et dolore magna aliqua. Ut enim ad minim veniam, quis</p>
  <a>LEARN MORE <svg class="arrow" width="14" height="14" viewBox="0 0 16 16"><circle cx="8" cy="8" r="7" fill="#1f5fc8"/><path d="M4 8h7M8 5l3 3-3 3" stroke="#fff" stroke-width="2" fill="none"/></svg></a>
</div>

<div class="abs partners" aria-label="Partners">
  <span><i></i>Tidewell Marine</span>
  <span><i></i>Harrowgate Wharves</span>
  <span><i></i>Lumen Cargo Handlers</span>
  <span><i></i>Ostrava Line</span>
  <span><i></i>Velko</span>
  <span><i></i>Maren Freight</span>
</div>

<footer class="abs footer">
  <div class="copy">© HARBOURLINE DATA SERVICES | ALL RIGHT RESERVED</div>
  <nav>LEGAL NOTICE<span>|</span>PRIVACY POLICY<span>|</span>CONTACT US</nav>
</footer>
</body>
</html>
```